We need a card and logo design for a new business based in Dallas Texas called Stonemarsh Financial LLC.

We provide bridge loans.We offer pay day loans,title loans and check cashing.Our products are emmergency loans that help borrowers meet short term liquidity needs until the next pay check.

The final design should communicate,professionalism,Sophistication and friendliness to our customers.Use the color Blue as much as possible and another eye catching color if possible.We will consider a profesional looking knight logo with the color Blue in it.Please design a full corporate identity.

```html
<!DOCTYPE html>
<html lang="en">
<head>
<meta charset="utf-8">
<title>Stonemarsh Financial LLC – Business Card</title>
<link rel="stylesheet" href="https://fonts.googleapis.com/css2?family=Montserrat:wght@700&family=Open+Sans:wght@400;600&display=swap">
<style>
  :root {
    --stage: #302c2a;
    --card-light: #ffffff;
    --card-dark-center: #3c4144;
    --card-dark-edge: #141516;
    --brand-blue: #1a56a6;
    --ink: #1e1e1e;
    --muted: #6a6a6a;
    --rule: #9a9a9a;
    --label: #e6e6e6;
  }
  * { box-sizing: border-box; margin: 0; padding: 0; }
  html, body {
    width: 1000px; height: 1200px; overflow: hidden;
    background: var(--stage);
    font-family: "Open Sans", Arial, sans-serif;
  }
  .canvas { position: relative; width: 1000px; height: 1200px; }
  .card {
    position: absolute; width: 723px; height: 423px;
  }
  .card--front { left: 140px; top: 119px; background: var(--card-light); }
  .card--back {
    left: 125px; top: 638px;
    background: radial-gradient(ellipse 55% 60% at 50% 45%, var(--card-dark-center), var(--card-dark-edge));
  }
  .brand {
    position: absolute; left: 0; right: 0;
    display: flex; align-items: center; justify-content: center; gap: 12px;
    font-family: "Open Sans", Arial, sans-serif; font-weight: 600;
    font-size: 30px; letter-spacing: 1px; text-transform: uppercase;
  }
  .brand__dot { width: 18px; height: 18px; border-radius: 50%; }
  .card--front .brand { top: 100px; color: var(--brand-blue); }
  .card--front .brand__dot { background: var(--brand-blue); }
  .card--back .brand { top: 178px; color: #ffffff; }
  .card--back .brand__dot { background: var(--brand-blue); }
  .holder { position: absolute; left: 36px; top: 262px; }
  .holder__name {
    font-family: "Montserrat", Arial, sans-serif; font-weight: 700;
    font-size: 19px; letter-spacing: 1.2px; color: var(--brand-blue);
    text-transform: uppercase; line-height: 20px;
  }
  .holder__title { font-size: 16px; color: var(--muted); line-height: 22px; }
  .divider {
    position: absolute; left: 361px; top: 249px; width: 2px; height: 130px;
    background: var(--rule);
  }
  .contact {
    position: absolute; right: 35px; top: 260px;
    text-align: right; font-size: 15.5px; color: var(--ink); line-height: 23px;
  }
  .contact__gap { margin-left: 20px; }
  .contact__address { margin-top: 18px; }
  .side-label {
    position: absolute; font-size: 20px; color: var(--label);
    font-family: "Open Sans", Arial, sans-serif;
  }
</style>
</head>
<body>
<main class="canvas">
  <section class="card card--front" aria-label="Card front">
    <div class="brand"><span class="brand__dot"></span>Stonemarsh Financial LLC</div>
    <div class="holder">
      <p class="holder__name">Dana Whitfield</p>
      <p class="holder__title">Financial Advisor</p>
    </div>
    <div class="divider"></div>
    <address class="contact" style="font-style:normal">
      <p>Tel: 555-010-2233<span class="contact__gap">Fax: 555-010-2233</span></p>
      <p>Email: info@stonemarshfinancial.com</p>
      <p class="contact__address">XXX Some Street Address</p>
      <p>State, Country</p>
    </address>
  </section>
  <p class="side-label" style="left:140px;top:589px">Front</p>

  <section class="card card--back" aria-label="Card back">
    <div class="brand"><span class="brand__dot"></span>Stonemarsh Financial LLC</div>
  </section>
  <p class="side-label" style="left:799px;top:1115px">Back</p>
</main>
</body>
</html>
```